Boutique custom software development company needs new business card

Our nearly 20 year old custom software development company would like to better include the fact that we are now providing Bitcoin services. These new services are B2B include education (how to acquire and securely hold Bitcoin) and integrating Bitcoin payments into existing ecommerce sites or other existing systems. Please keep the card clean and simple. Attached is our current design and some other files. vextorial.com

Target Market(s)

businesses owners interested in long term relationship

Industry/Entity Type

Custom software development and Bitcoin

Contact Information for Business Card

Dale Parker, dale@vextorial.com, vextorial.com, (888) 555-VXTRL

Font styles to use
Other font styles liked:
• monospace

Requirements
Must have
• double-sided
Nice to have
• clean and simple
Should not have
• physical address

```html
<!DOCTYPE html>
<html lang="en">
<head>
<meta charset="utf-8">
<title>vextorial business card</title>
<link rel="stylesheet" href="https://fonts.googleapis.com/css2?family=Open+Sans:wght@400;700&family=Space+Mono:wght@700&family=Courier+Prime&display=swap">
<style>
  :root {
    --bg: #d6d6d3;
    --card: #ffffff;
    --blue: #3f73b8;
    --orange: #ef7b22;
    --ink: #1d1d1d;
  }
  * { margin: 0; padding: 0; box-sizing: border-box; }
  html, body { width: 1200px; height: 801px; overflow: hidden; }
  body {
    background: var(--bg);
    display: flex;
    align-items: center;
    justify-content: center;
    gap: 40px;
    font-family: "Open Sans", sans-serif;
  }
  .card {
    position: relative;
    width: 540px;
    height: 309px;
    background: var(--card);
    border-radius: 16px;
    border-bottom: 3px solid var(--blue);
    overflow: hidden;
  }
  .wordmark {
    font-family: "Open Sans", sans-serif;
    font-weight: 700;
    color: var(--blue);
    letter-spacing: -0.5px;
    line-height: 1;
    white-space: nowrap;
  }
  .tagline {
    font-family: "Open Sans", sans-serif;
    font-weight: 400;
    color: var(--blue);
    white-space: nowrap;
  }

  /* Front side */
  .front-brand {
    position: absolute;
    top: 34px;
    right: 34px;
    text-align: right;
  }
  .front-brand .wordmark { font-size: 40px; }
  .front-brand .tagline { font-size: 14px; margin-top: 4px; }
  .brand-square {
    position: absolute;
    left: 34px;
    top: 50px;
    width: 96px;
    height: 96px;
    background: var(--blue);
  }
  .divider {
    position: absolute;
    left: 270px;
    top: 176px;
    width: 240px;
    height: 1.5px;
    background: var(--orange);
  }
  .edge-tab {
    position: absolute;
    left: 0;
    top: 186px;
    width: 12px;
    height: 44px;
    background: var(--orange);
  }
  .person {
    position: absolute;
    left: 34px;
    top: 186px;
  }
  .person-name {
    font-family: "Space Mono", monospace;
    font-weight: 700;
    font-size: 24px;
    color: var(--orange);
    line-height: 1.1;
  }
  .person-role {
    font-family: "Courier Prime", monospace;
    font-size: 13px;
    color: var(--ink);
  }
  .contacts {
    position: absolute;
    left: 34px;
    top: 242px;
    list-style: none;
    font-family: "Courier Prime", monospace;
    font-size: 13px;
    color: var(--ink);
    line-height: 1.45;
  }
  .contacts li { display: flex; align-items: center; gap: 7px; }
  .contacts svg { width: 11px; height: 11px; fill: var(--orange); flex: none; }
  .services {
    position: absolute;
    right: 34px;
    top: 192px;
    text-align: right;
    list-style: none;
    font-family: "Courier Prime", monospace;
    font-size: 12px;
    color: var(--ink);
    line-height: 1.5;
  }
  .services-title { color: var(--orange); font-weight: 700; }

  /* Back side */
  .back-brand {
    position: absolute;
    left: 50%;
    top: 50%;
    transform: translate(-50%, -50%);
    text-align: left;
  }
  .back-brand .wordmark { font-size: 84px; }
  .back-brand .tagline { font-size: 27px; margin-top: 6px; }
</style>
</head>
<body>

  <section class="card card-front" aria-label="Business card front">
    <div class="brand-square"></div>

    <div class="front-brand">
      <div class="wordmark">vextorial</div>
      <div class="tagline">developer of custom applications</div>
    </div>

    <div class="edge-tab"></div>
    <div class="divider"></div>

    <div class="person">
      <div class="person-name">Dale Parker</div>
      <div class="person-role">Founding Partner</div>
    </div>

    <ul class="contacts">
      <li>
        <svg viewBox="0 0 24 24" aria-hidden="true"><path d="M6.6 10.8a15 15 0 0 0 6.6 6.6l2.2-2.2c.3-.3.7-.4 1-.2 1.1.4 2.3.6 3.6.6.6 0 1 .4 1 1V20c0 .6-.4 1-1 1A17 17 0 0 1 3 4c0-.6.4-1 1-1h3.5c.6 0 1 .4 1 1 0 1.3.2 2.5.6 3.6.1.3 0 .7-.2 1z"/></svg>
        (888) 555-VXTRL
      </li>
      <li>
        <svg viewBox="0 0 24 24" aria-hidden="true"><path d="M2 5h20v14H2z M2 5l10 8 10-8"/></svg>
        dale@vextorial.com
      </li>
      <li>
        <svg viewBox="0 0 24 24" aria-hidden="true"><circle cx="12" cy="12" r="10"/></svg>
        www.vextorial.com
      </li>
    </ul>

    <ul class="services">
      <li class="services-title">Bitcoin services</li>
      <li>Bitcoin education</li>
      <li>Payment integration</li>
    </ul>
  </section>

  <section class="card card-back" aria-label="Business card back">
    <div class="back-brand">
      <div class="wordmark">vextorial</div>
      <div class="tagline">developer of custom applications</div>
    </div>
  </section>

</body>
</html>
```